Harwick Moss Fine Art gallery website - Modern british art for sale

We need a website design that is both current and high end. Our products are expensive and this should be reflected in the look of the website. We would like the logo we had designed last year to be clearly seen in the design. We want sleek, simple, and easy to navigate. Nothing too colourful as the colours of the art should always take precedence.

Target Market(s)

The average price of one our products starts at £250 and can go up to £10,000 we are an entry level gallery.

Industry/Entity Type

Art Gallery

Number of Pages Required

5+ page

Font styles to use
Sans Serif

Colors
000000
ffffff
faa54b
abd037
886aae
b868aa

Requirements
Must have
• Attractive front page. Linked to our Twitter feed.
• 4 links from front page - New Releases, about us, Artists, contact us
• Social media links - Facebook, Twitter, YouTube, Instagram.
• Each artist must have their own page, each page must have a biography link to another page.
Nice to have
• Utilise our new logo design. I would like the Twitter feed to link to the front page in a small way so you can see what's being said on Twitter by the company. For future proofing maybe have a locations function on the front page which can be adroit down menu showing where our other galleries are.

```html
<!DOCTYPE html>
<html lang="en">
<head>
<meta charset="utf-8">
<title>Harwick Moss Fine Art</title>
<link href="https://fonts.googleapis.com/css2?family=Open+Sans:wght@400;600;700&family=Playfair+Display:ital,wght@1,400&display=swap" rel="stylesheet">
<style>
:root{
  --ink:#2b2b2b;
  --muted:#8a8a8a;
  --line:#e4e4e4;
  --white:#ffffff;
  --purple:#886aae;
  --orange:#ee6a2f;
  --gold:#faa54b;
  --green:#abd037;
  --pink:#b868aa;
  --teal:#3fb8c9;
  --footer:#f4f4f4;
}
*{box-sizing:border-box;margin:0;padding:0}
html,body{width:1200px;height:2484px;overflow:hidden;background:var(--white)}
body{position:relative;font-family:"Open Sans",Arial,sans-serif;color:var(--ink)}
.abs{position:absolute}
.topstrip{left:0;top:0;width:1200px;height:6px;background:linear-gradient(90deg,var(--purple) 0 25%,var(--green) 25% 50%,var(--gold) 50% 75%,var(--pink) 75%)}
/* header */
.logo{left:118px;top:44px;display:flex;align-items:center;gap:12px}
.logo-dot{width:30px;height:30px;border-radius:50%;background:var(--teal)}
.logo-name{font-size:34px;font-weight:400;color:#555;letter-spacing:1px;white-space:nowrap}
.cart{right:118px;top:46px;display:flex;align-items:center;gap:10px;font-size:13px;color:var(--muted)}
.cart-icon{width:30px;height:30px;border:2px solid var(--orange);border-radius:50%;display:flex;align-items:center;justify-content:center}
.nav{right:118px;top:100px;display:flex;gap:46px;align-items:center;font-size:13px;font-weight:600;letter-spacing:.5px;color:#555}
.nav .active{color:var(--purple);border-bottom:3px solid var(--purple);padding-bottom:6px}
/* hero */
.hero{left:0;top:162px;width:1200px;height:538px;background:linear-gradient(100deg,#5a5a5a 0%,#474747 45%,#303030 100%)}
.hero-text{left:830px;top:268px;color:var(--white)}
.hero-kicker{font-size:46px;font-weight:700;letter-spacing:1px;line-height:1.1}
.hero-title{font-family:"Playfair Display",Georgia,serif;font-style:italic;font-size:54px;line-height:1.1;white-space:nowrap}
.hero-price{margin-top:14px;font-size:15px;font-weight:700;letter-spacing:1px}
.hero-price b{color:var(--gold);font-size:40px;font-style:italic;margin-left:6px}
.hero-copy{margin-top:10px;font-size:13px;width:280px;line-height:1.5;color:#ddd}
.btn{display:inline-block;background:var(--orange);color:var(--white);font-size:13px;font-weight:600;padding:11px 24px;border-radius:22px}
.hero-text .btn{margin-top:18px}
.arrow{top:400px;width:50px;height:50px;border:2px solid rgba(255,255,255,.7);border-radius:50%}
/* about */
.about{left:118px;top:780px;width:620px}
h2.section{font-size:30px;font-weight:600;letter-spacing:1px;color:#444}
.about p{font-size:13px;line-height:1.75;color:var(--muted);margin-top:22px}
.about .btn{margin-top:32px}
.about-ring{left:748px;top:746px;width:320px;height:320px;border-radius:50%;border:10px solid var(--purple)}
.about-photo{left:760px;top:758px;width:296px;height:296px;border-radius:50%;background:linear-gradient(160deg,#f5f5f5,#cfcfcf 60%,#7d7d7d)}
/* new releases */
.wave{left:0;top:1080px;width:1200px;height:760px}
.releases{left:118px;top:1270px;width:964px;color:var(--white)}
.releases h2{color:var(--white)}
.releases p{font-size:13px;line-height:1.6;margin-top:10px;opacity:.9;width:760px}
.product{top:1390px;width:190px;text-align:center;color:var(--white)}
.frame{width:190px;height:240px;border:14px solid #3a2a1c;box-shadow:0 4px 10px rgba(0,0,0,.3)}
.product .name{font-size:12px;font-weight:600;margin-top:14px}
.product .price{font-size:14px;color:var(--gold);font-weight:700;margin-top:4px}
.product .add{display:inline-block;margin-top:8px;background:var(--white);color:var(--ink);font-size:11px;font-weight:600;padding:6px 16px;border-radius:14px}
/* twitter */
.tw-title{left:0;top:1920px;width:1200px;text-align:center}
.tweet{top:1990px;width:470px;height:120px;border:1px solid var(--line);padding:18px;display:flex;gap:16px;background:var(--white)}
.avatar{width:70px;height:70px;flex:none;background:linear-gradient(135deg,#777,#333)}
.tweet .meta{font-size:12px;color:var(--purple);font-weight:600}
.tweet .meta span{color:var(--muted);font-weight:400}
.tweet p{font-size:12px;color:#666;line-height:1.55;margin-top:6px}
.tweet .link{color:var(--purple)}
/* footer */
.footer{left:0;top:2190px;width:1200px;height:294px;background:var(--footer);border-top:6px solid var(--purple)}
.f-col{top:2220px;font-size:12px;color:var(--muted);line-height:1.9}
.f-col h4{font-size:13px;color:#444;font-weight:700;letter-spacing:.5px;margin-bottom:8px}
.f-logo{font-size:18px;color:#555;display:flex;align-items:center;gap:8px;margin-bottom:10px;white-space:nowrap;line-height:1.4}
.f-logo i{width:16px;height:16px;border-radius:50%;background:var(--teal);display:inline-block;flex:none}
.c-row{display:flex;gap:8px;align-items:center;white-space:nowrap}
.c-row svg{flex:none}
.f-bottom{left:118px;top:2432px;width:964px;border-top:1px solid var(--line);padding-top:12px;display:flex;justify-content:space-between;align-items:center;font-size:11px;color:var(--muted)}
.social{display:flex;gap:8px;align-items:center}
.social i{width:24px;height:24px;border-radius:50%;background:var(--orange);display:inline-block}
</style>
</head>
<body>
<div class="abs topstrip"></div>

<div class="abs logo"><span class="logo-dot"></span><span class="logo-name">Harwick Moss Fine Art</span></div>
<div class="abs cart"><span class="cart-icon"><svg width="14" height="14" viewBox="0 0 14 14"><path d="M1 2h2l2 7h6l2-5H4" fill="none" stroke="#ee6a2f" stroke-width="1.5"/><circle cx="6" cy="12" r="1" fill="#ee6a2f"/><circle cx="10" cy="12" r="1" fill="#ee6a2f"/></svg></span>MY CART · £0</div>
<nav class="abs nav">
  <span class="active">HOME</span><span>NEW RELEASES</span><span>ABOUT US</span><span>ARTISTS</span><span>CONTACT US</span>
  <svg width="16" height="16" viewBox="0 0 16 16"><circle cx="7" cy="7" r="5" fill="none" stroke="#555" stroke-width="2"/><path d="M11 11l4 4" stroke="#555" stroke-width="2"/></svg>
</nav>

<div class="abs hero" role="img" aria-label="Photo of a hand drawing with a pencil beside framed sketches on a dark brick wall"></div>
<div class="abs arrow" style="left:30px"><svg width="46" height="46" viewBox="0 0 46 46"><path d="M26 15l-8 8 8 8" fill="none" stroke="#fff" stroke-width="2"/></svg></div>
<div class="abs arrow" style="right:30px"><svg width="46" height="46" viewBox="0 0 46 46"><path d="M20 15l8 8-8 8" fill="none" stroke="#fff" stroke-width="2"/></svg></div>
<div class="abs hero-text">
  <div class="hero-kicker">HARWICK</div>
  <div class="hero-title">Moss Fineart</div>
  <div class="hero-price">PRICE STARTING AT <b>£250</b></div>
  <div class="hero-copy">Original modern British art, chosen with care and framed ready to hang in your home today.</div>
  <span class="btn">Buy Now Today</span>
</div>

<section class="abs about">
  <h2 class="section">ABOUT US</h2>
  <p>We are a small gallery with a love of modern British art. Every piece we show is picked by hand from artists we know well, so you can buy with trust and enjoy work that feels personal. Our prices start low so that new collectors can begin their own story.</p>
  <p>From bold prints to quiet pencil studies, our range changes every month as new works arrive. Visit us in person or browse online, and our friendly team will help you find the right piece for your walls and your budget.</p>
  <span class="btn">Buy Now Today</span>
</section>
<div class="abs about-ring"></div>
<div class="abs about-photo" role="img" aria-label="Sketch of a church tower and town buildings"></div>

<svg class="abs wave" viewBox="0 0 1200 760" preserveAspectRatio="none" aria-hidden="true">
  <path d="M0 110 C300 30 800 20 1200 0 L1200 700 C800 760 400 760 0 720 Z" fill="#886aae"/>
</svg>
<section class="abs releases">
  <h2 class="section">NEW RELEASES</h2>
  <p>Fresh works from our artists arrive every week. Take a look at the latest pieces added to the gallery and add your favourite to the cart before it is gone.</p>
</section>
<div class="abs product" style="left:132px"><div class="frame" role="img" aria-label="Print of a dancer on a pale background" style="background:linear-gradient(160deg,#f1f1f1,#a9a9a9)"></div><div class="name">Small Northern Town A.1</div><div class="price">£250.00</div><span class="add">add to cart</span></div>
<div class="abs product" style="left:382px"><div class="frame" role="img" aria-label="Abstract print of bright geometric shapes" style="background:linear-gradient(135deg,#f5a83f,#e24c6a,#7f5fb0)"></div><div class="name">Small Northern Town A.2</div><div class="price">£250.00</div><span class="add">add to cart</span></div>
<div class="abs product" style="left:632px"><div class="frame" role="img" aria-label="Print of a town skyline with a blue sky" style="background:linear-gradient(180deg,#6cc5e6,#c9c9c9 55%,#5a5a5a)"></div><div class="name">Small Northern Town A.3</div><div class="price">£250.00</div><span class="add">add to cart</span></div>
<div class="abs product" style="left:882px"><div class="frame" role="img" aria-label="Print of coloured stripes on white" style="background:linear-gradient(90deg,#f7f7f7,#3d7fc1 35%,#f2b533 65%,#e85a3a)"></div><div class="name">Small Northern Town A.4</div><div class="price">£250.00</div><span class="add">add to cart</span></div>

<h2 class="abs section tw-title">TWITTER FEED</h2>
<div class="abs tweet" style="left:118px"><div class="avatar" role="img" aria-label="Gallery profile picture"></div><div><div class="meta">@HarwickMossArt <span>· 12 Apr</span></div><p>So sorry for the late post today. All of our pieces are now framed with a free print, see the gallery for more <span class="link">harwickmossart.co.uk</span></p></div></div>
<div class="abs tweet" style="left:612px"><div class="avatar" role="img" aria-label="Gallery profile picture"></div><div><div class="meta">@HarwickMossArt <span>· 10 Apr</span></div><p>So sorry for the late post today. All of our pieces are now framed with a free print, see the gallery for more <span class="link">harwickmossart.co.uk</span></p></div></div>

<div class="abs footer"></div>
<div class="abs f-col" style="left:118px;width:236px">
  <div class="f-logo"><i></i>Harwick Moss Fine Art</div>
  We are a small gallery of modern British art, with fair prices and a warm welcome for every new collector.
</div>
<div class="abs f-col" style="left:380px"><h4>QUICK LINKS</h4>Home<br>New Releases<br>About Us<br>Artists<br>Contact Us</div>
<div class="abs f-col" style="left:530px"><h4>EXTRAS</h4>Brands<br>Gift Vouchers<br>Our Artists<br>Locations<br>Specials</div>
<div class="abs f-col" style="left:690px"><h4>MY ACCOUNT</h4>My Account<br>Order History<br>Wish List<br>Newsletter</div>
<div class="abs f-col" style="left:858px;width:230px"><h4>CONTACT US</h4>
  <div class="c-row"><svg width="12" height="14" viewBox="0 0 12 14"><path d="M6 13C2 8 1 6 1 5a5 5 0 0110 0c0 1-1 3-5 8z" fill="#886aae"/></svg>14 Mill Lane, Harwick, HW2 4PL</div>
  <div class="c-row"><svg width="12" height="12" viewBox="0 0 12 12"><path d="M2 1h3l1 3-2 1a7 7 0 003 3l1-2 3 1v3a1 1 0 01-1 1A10 10 0 011 2a1 1 0 011-1z" fill="#886aae"/></svg>01632 960 418</div>
  <div class="c-row"><svg width="12" height="10" viewBox="0 0 12 10"><rect x="0.5" y="0.5" width="11" height="9" fill="none" stroke="#886aae"/><path d="M1 1l5 4 5-4" fill="none" stroke="#886aae"/></svg>info@harwickmossart.co.uk</div>
</div>
<div class="abs f-bottom"><span>Copyright © 2015 Harwick Moss Fine Art. All Rights Reserved.</span><span class="social">Follow us <i></i><i></i><i></i><i></i></span></div>
</body>
</html>
```